Values and Organizational Purpose Signage

We recently solidified our company values, organizatioanal purpose and strategic vision. I'd like to develop some tasteful (not overly corporate) signage of these values to display in our office.

I've attached the hand-written values and purpose that my core team members then initialed acknowleding they align along with the signage at the front of our office to provide some perspective on our brand identity.

Industry/Entity Type

It Company

Font styles to use
Sans Serif

Requirements
Must have
• I'd like to see the values and org purpose depicted as one sign and as separate signs (i.e., values on one sign and org purpose on another). I need it to reflect our brand identity which I've uploaded

```html
<!DOCTYPE html>
<html lang="en">
<head>
<meta charset="utf-8">
<title>Values and Organizational Purpose</title>
<link rel="stylesheet" href="https://fonts.googleapis.com/css2?family=Noto+Serif:wght@400&display=swap">
<style>
  :root {
    --accent: #bfd330;
    --ink: #3f454d;
    --frame: #474d54;
    --rule: #6e6e6e;
    --paper: #ffffff;
  }
  * { margin: 0; padding: 0; box-sizing: border-box; }
  html, body {
    width: 1200px; height: 917px; overflow: hidden;
    background: var(--paper);
  }
  .sign {
    position: relative;
    width: 1200px; height: 917px;
    border: 4px solid var(--frame);
    background: var(--paper);
    font-family: "Noto Serif", serif;
    color: var(--ink);
  }
  .sign > * { position: absolute; }
  .heading-large {
    font-size: 50px; line-height: 63px;
    color: var(--accent); font-weight: 400;
  }
  .rule { height: 2px; background: var(--rule); }
  .purpose-title { left: 75px; top: 273px; width: 400px; }
  .purpose-rule { left: 74px; top: 419px; width: 262px; }
  .purpose-text {
    left: 75px; top: 454px; width: 360px;
    font-size: 31px; line-height: 42px;
  }
  .values-title { left: 636px; top: 82px; width: 400px; }
  .values-rule { left: 632px; top: 229px; width: 262px; }
  .value { left: 636px; width: 480px; }
  .value-name {
    font-size: 42px; line-height: 50px;
    color: var(--accent); font-weight: 400;
  }
  .value-text {
    font-size: 23px; line-height: 31.5px;
    position: absolute; left: 2px; width: 470px;
  }
  .value-respect { top: 256px; }
  .value-respect .value-text { top: 52px; }
  .value-integrity { top: 401px; }
  .value-integrity .value-text { top: 60px; }
  .value-excellence { top: 511px; }
  .value-excellence .value-text { top: 60px; }
  .value-openness { top: 643px; }
  .value-openness .value-text { top: 53px; }
  .brand {
    left: 0; width: 1192px; top: 824px;
    display: flex; justify-content: center; align-items: center; gap: 7px;
  }
  .brand-square { width: 10px; height: 10px; background: var(--accent); }
  .brand-name { font-size: 20px; line-height: 24px; color: var(--ink); }
</style>
</head>
<body>
  <main class="sign">
    <h1 class="heading-large purpose-title">Organizational<br>Purpose</h1>
    <div class="rule purpose-rule"></div>
    <p class="purpose-text">We deliver simple and digestible solutions to complex matters.</p>

    <h2 class="heading-large values-title">Core Values<br>Defines</h2>
    <div class="rule values-rule"></div>

    <section class="value value-respect">
      <h3 class="value-name">Respect</h3>
      <p class="value-text">We are transparent and receptive to the thoughts, opinions, and feelings to others</p>
    </section>
    <section class="value value-integrity">
      <h3 class="value-name">Integrity</h3>
      <p class="value-text">We uphold our promises</p>
    </section>
    <section class="value value-excellence">
      <h3 class="value-name">Excellence</h3>
      <p class="value-text">We continuously strive to be the best in all endeavors</p>
    </section>
    <section class="value value-openness">
      <h3 class="value-name">Open mindedness</h3>
      <p class="value-text">We encourage creative and innovative expressions</p>
    </section>

    <footer class="brand">
      <span class="brand-square"></span>
      <span class="brand-name">Northvale</span>
    </footer>
  </main>
</body>
</html>
```